Social Media Graphics - Oakline Push REVISED

Create 6-7 individual social media graphics (square size) to encourage folks to join our online course called:

The Harvest Ledger Circle
How to Launch a Multi-Million Business From Scratch
Sign Up Today!

IMPORTANT: Make the largest and most prominent text on the graphic be: How to Launch a Multi-Million Business From Scratch

For the color scheme of the graphics, let's try a blue color palette; make sure the graphics appeal to both men and women

Make sure each graphic contains 1 of the 3 pics attached (crop pic as needed); and make sure one of the graphics is all TEXT only.

Target Market(s)

men and women looking to start a business

Industry/Entity Type

Entrepreneurship

Colors
0054AA
0677BA
7BADD7
CADEEF
E8F1F8

Requirements
Must have
• All the text and use the 3 pics provided; one graphic can be all text; Simple, modern design that's easy to read

```html
<!DOCTYPE html>
<html lang="en">
<head>
<meta charset="UTF-8">
<title>The Harvest Ledger Circle – Sign Up</title>
<link href="https://fonts.googleapis.com/css2?family=Exo+2:ital,wght@1,700;1,800;1,900&display=swap" rel="stylesheet">
<style>
  :root {
    --brand-blue: #0054AA;
    --mid-blue: #0677BA;
    --sky-blue: #7BADD7;
    --pale-blue: #CADEEF;
    --mist-blue: #E8F1F8;
    --accent-blue: #3FA9F5;
    --white: #FFFFFF;
    --navy: #0B2A4A;
    --cyan: #35D3F0;
  }
  html, body {
    margin: 0;
    padding: 0;
    width: 1200px;
    height: 1200px;
    overflow: hidden;
    background: var(--brand-blue);
  }
  .poster {
    position: relative;
    width: 1200px;
    height: 1200px;
    overflow: hidden;
    background: var(--brand-blue);
    font-family: 'Exo 2', sans-serif;
    font-style: italic;
  }
  .backdrop {
    position: absolute;
    inset: 0;
  }
  .course-name {
    position: absolute;
    top: 64px;
    left: 0;
    width: 100%;
    margin: 0;
    text-align: center;
    color: var(--white);
    text-transform: uppercase;
    font-weight: 900;
    font-size: 58px;
    line-height: 1;
    letter-spacing: 1px;
  }
  .course-name .highlight {
    background: linear-gradient(180deg, #6CC4FF 0%, var(--accent-blue) 55%, #1C7FD8 100%);
    -webkit-background-clip: text;
    background-clip: text;
    color: transparent;
  }
  .headline {
    position: absolute;
    top: 160px;
    left: 40px;
    width: 1120px;
    margin: 0;
    text-align: center;
    color: var(--white);
    text-transform: uppercase;
    font-weight: 900;
    font-size: 74px;
    line-height: 1.08;
    letter-spacing: 1px;
  }
  .hosts-photo {
    position: absolute;
    left: 238px;
    top: 566px;
    width: 796px;
    height: 634px;
    border-radius: 260px 260px 0 0;
    background: linear-gradient(90deg, #1A1D24 0%, #2B2F38 45%, #1F4E85 70%, #2A5C94 100%);
  }
  .cta {
    position: absolute;
    left: 340px;
    top: 1066px;
    width: 520px;
    height: 96px;
    border-radius: 48px;
    border: 5px solid var(--navy);
    box-sizing: border-box;
    background: linear-gradient(180deg, #7FF0FF 0%, var(--cyan) 45%, #169BD0 100%);
    box-shadow: inset 0 0 0 4px rgba(255,255,255,0.55);
    display: flex;
    align-items: center;
    justify-content: center;
    color: var(--white);
    text-transform: uppercase;
    font-weight: 900;
    font-size: 50px;
    letter-spacing: 1px;
    text-shadow: 0 2px 3px rgba(11,42,74,0.6);
  }
</style>
</head>
<body>
  <div class="poster">
    <svg class="backdrop" width="1200" height="1200" viewBox="0 0 1200 1200" aria-hidden="true">
      <polygon class="backdrop__lower-band" points="17,878 420,965 520,1200 110,1200" fill="var(--mid-blue)"/>
      <polygon class="backdrop__triangle" points="839,498 1067,1200 467,1200" fill="var(--white)"/>
    </svg>

    <p class="course-name">The <span class="highlight">Harvest Ledger</span> Circle</p>

    <h1 class="headline">How to launch a<br>multi-million business<br>from scratch</h1>

    <div class="hosts-photo" role="img" aria-label="Photo of the two course hosts standing side by side, smiling"></div>

    <div class="cta">Sign up today!</div>
  </div>
</body>
</html>
```